Personal training and nutrition business needs business card design

We need a business card that outlays our services and invites potential customers to join our team and take the first step to a healthier and more enjoyable life. We cater for any level of fitness and specialize in weight loss and conditioning, strength training, muscle gain and strength endurance. Whether you are just starting off or need some help getting to the next level of your journey we are here to get the job done.
We specialize in one on one or one on two personal training sessions and each program will be custom made to suit individual fitness goals of our clients

```html
<!DOCTYPE html>
<html lang="en">
<head>
<meta charset="utf-8">
<title>Stride &amp; Tempo – Business Card</title>
<link href="https://fonts.googleapis.com/css2?family=Exo+2:ital,wght@0,800;1,800&family=Oswald:wght@500&family=Roboto:wght@400&display=swap" rel="stylesheet">
<style>
  :root {
    --backdrop: #2a2a2a;
    --card: #efefef;
    --ink: #141414;
    --text: #2c2c2c;
    --purple: #7a3fa0;
    --violet: #5d3a9c;
    --orchid: #a0509a;
  }
  * { margin: 0; padding: 0; box-sizing: border-box; }
  html, body { width: 1200px; height: 1138px; overflow: hidden; }
  body { background: var(--backdrop); position: relative; font-family: "Roboto", sans-serif; }

  .card {
    position: absolute; left: 289px; width: 622px; height: 376px;
    background: linear-gradient(160deg, #f4f4f4, #e6e6e6);
    border-radius: 16px; overflow: hidden;
  }
  .card--front { top: 186px; }
  .card--back { top: 608px; }

  .brand { display: flex; align-items: center; gap: 12px; color: var(--ink);
    font-family: "Exo 2", sans-serif; font-weight: 800; text-transform: uppercase; letter-spacing: 1px; }
  .brand__mark { width: 44px; height: 44px; background: var(--purple); flex: none; }

  .tagline { font-family: "Oswald", sans-serif; font-weight: 500; color: var(--purple);
    text-transform: uppercase; letter-spacing: 1.5px; }

  /* front */
  .front__brand { position: absolute; top: 150px; left: 0; right: 0; justify-content: center; font-size: 40px; }
  .front__tagline { position: absolute; top: 252px; left: 0; right: 0; text-align: center; font-size: 13px; }
  .front__web { position: absolute; top: 320px; left: 0; right: 0; display: flex; justify-content: center;
    align-items: center; gap: 18px; font-size: 16px; color: var(--ink); }
  .front__web .rule { width: 70px; height: 2px; background: var(--ink); }
  .front__band { position: absolute; bottom: 0; left: 0; right: 0; height: 9px;
    background: linear-gradient(90deg, var(--orchid), var(--violet)); }
  .hl { color: var(--purple); }

  /* back */
  .back__brand { position: absolute; left: 82px; top: 120px; font-size: 31px; line-height: 1.05;
    flex-direction: column; align-items: flex-start; gap: 14px; }
  .back__brand .brand__mark { width: 52px; height: 52px; margin-left: 60px; }
  .back__tagline { position: absolute; left: 82px; top: 272px; font-size: 8.5px; letter-spacing: 0.8px; }

  .contact { position: absolute; left: 342px; top: 86px; color: var(--text); }
  .contact__name { font-family: "Exo 2", sans-serif; font-style: italic; font-weight: 800;
    font-size: 23px; color: var(--purple); text-transform: uppercase; letter-spacing: 0.5px; }
  .contact__role { font-size: 15.5px; margin-top: 2px; }
  .contact__list { list-style: none; margin-top: 26px; font-size: 15.5px; }
  .contact__list li { display: flex; align-items: center; gap: 14px; height: 24px; }
  .contact__list svg { width: 14px; height: 14px; fill: var(--purple); flex: none; }
  .contact__address { font-size: 15.5px; line-height: 24px; margin-top: 7px; }
</style>
</head>
<body>
  <section class="card card--front">
    <div class="brand front__brand"><span class="brand__mark"></span>Stride &amp; Tempo</div>
    <p class="tagline front__tagline">Personal Training.&nbsp; Nutrition. Motivation</p>
    <p class="front__web"><span class="rule"></span><span>www.<span class="hl">strideandtempo</span>.com</span><span class="rule"></span></p>
    <div class="front__band"></div>
  </section>

  <section class="card card--back">
    <div class="brand back__brand"><span class="brand__mark"></span><span>Stride<br>&amp; Tempo</span></div>
    <p class="tagline back__tagline">Personal Training.&nbsp; Nutrition. Motivation</p>

    <div class="contact">
      <h1 class="contact__name">Marcus Reyes</h1>
      <p class="contact__role">Personal Trainer</p>
      <ul class="contact__list">
        <li><svg viewBox="0 0 16 16"><path d="M2 5c0-2 2-3 6-3s6 1 6 3v1h-3V5H5v1H2zM4 7h8l2 7H2z"/></svg>+1 (555) 204-7731</li>
        <li><svg viewBox="0 0 16 16"><path d="M1 3h14v10H1zM2 4l6 5 6-5v1L8 10 2 5z" fill-rule="evenodd"/></svg>marcus@strideandtempo.com</li>
        <li><svg viewBox="0 0 16 16"><path d="M8 1a7 7 0 1 0 0 14A7 7 0 0 0 8 1zm0 1.5c1 1 1.7 2.7 1.8 4.5H6.2C6.3 5.2 7 3.5 8 2.5zM2.6 7h2.1c.1-1.6.5-3 1.2-4A5.5 5.5 0 0 0 2.6 7zm8.7 0h2.1a5.5 5.5 0 0 0-3.3-4c.7 1 1.1 2.4 1.2 4zM2.6 9a5.5 5.5 0 0 0 3.3 4c-.7-1-1.1-2.4-1.2-4zm3.6 0c.1 1.8.8 3.5 1.8 4.5 1-1 1.7-2.7 1.8-4.5zm5.1 0c-.1 1.6-.5 3-1.2 4a5.5 5.5 0 0 0 3.3-4z"/></svg>www.<span class="hl">strideandtempo</span>.com</li>
      </ul>
      <p class="contact__address">1482 Cedar Ridge Lane<br>Oakdale Texas 75102</p>
    </div>
  </section>
</body>
</html>
```